KVOR Individual and Corporate Development Business Card Design

KVOR needs a business card design that is aligned with it's values and targetted markets. Coherent Lattice of Adaptive Reasoning Method's self diagnosis model and tools, which can be used for personal improvement and team/business performance enhancement, is based on the learnings of over 20 years of medical practitioning. KVOR supercharges personal effectiveness and awareness to also increase team and business performance.

The targetted markets are high performance individuals and teams who aspire seek to enhance their capabilities and achieve their absolute best potential.

Look and feel for the business card design we are looking for is high technology, premium, fresh, new and medical.

Target Market(s)

Industry/Entity Type

Business Consultant

Contact Information for Business Card

Logo, Full Name, Title, Phone number, Email, company name, Address,

Font styles to use
Sans Serif

Requirements
Must have
• Tag line: Maximising Performance for Highly Effective People
• Please use same colours as the logo.

```html
<!DOCTYPE html>
<html lang="en">
<head>
<meta charset="utf-8">
<title>KVOR Business Card</title>
<link href="https://fonts.googleapis.com/css2?family=Open+Sans:wdth,wght@75..100,400;75..100,600;75..100,700&display=swap" rel="stylesheet">
<style>
  :root {
    --stage: #000000;
    --card-light: #f3f3f3;
    --teal: #03a9c2;
    --ink: #3a3a3a;
    --white: #ffffff;
  }
  html, body {
    margin: 0;
    padding: 0;
    width: 1200px;
    height: 900px;
    overflow: hidden;
    background: var(--stage);
    font-family: "Open Sans", Arial, sans-serif;
  }
  .canvas {
    position: relative;
    width: 1200px;
    height: 900px;
  }
  .card {
    position: absolute;
    top: 200px;
    width: 310px;
    height: 502px;
    box-sizing: border-box;
  }
  .card--front {
    left: 265px;
    background: var(--card-light);
    border-radius: 52px 0 52px 0;
  }
  .card--back {
    left: 641px;
    width: 309px;
    background: var(--teal);
    border-radius: 0 52px 0 52px;
  }
  .brand {
    position: absolute;
    left: 0;
    right: 0;
    text-align: center;
  }
  .brand__name {
    display: block;
    font-weight: 700;
    font-size: 58px;
    line-height: 1;
    letter-spacing: 3px;
  }
  .brand__full {
    display: block;
    margin-top: 12px;
    font-weight: 600;
    font-size: 13.5px;
    line-height: 16px;
    letter-spacing: 0.2px;
    text-transform: uppercase;
  }
  .card--front .brand { top: 84px; color: var(--teal); }
  .card--back .brand { top: 368px; color: var(--white); }

  .contact {
    position: absolute;
    left: 27px;
    top: 326px;
    color: var(--ink);
    font-size: 13.5px;
    line-height: 16px;
    text-transform: uppercase;
  }
  .contact__name {
    margin: 0;
    color: var(--teal);
    font-weight: 600;
    font-size: 17px;
    line-height: 22px;
  }
  .contact__title { margin: 3px 0 0; }
  .contact__address { margin: 18px 0 0; }
  .contact__lines { list-style: none; margin: 12px 0 0; padding: 0; }
  .contact__lines li {
    display: flex;
    align-items: center;
    gap: 6px;
    height: 19px;
  }
  .contact__icon { width: 10px; height: 10px; fill: var(--teal); }

  .tagline {
    position: absolute;
    left: 16px;
    right: 18px;
    top: 44px;
    margin: 0;
    color: var(--white);
    font-weight: 600;
    font-stretch: 88%;
    text-transform: uppercase;
    text-align: center;
    line-height: 1;
  }
  .tagline span { display: block; }
  .tagline__l1 { font-size: 45px; letter-spacing: 1px; }
  .tagline__l2 { font-size: 36px; margin-top: 10px; letter-spacing: 0.5px; }
  .tagline__l3 { font-size: 46px; margin-top: 6px; }
  .tagline__l4 { font-size: 51px; margin-top: 2px; }
  .tagline__l5 { font-size: 70px; margin-top: -2px; letter-spacing: 1px; }
</style>
</head>
<body>
<main class="canvas">
  <section class="card card--front" aria-label="Business card front">
    <div class="brand">
      <span class="brand__name">KVOR</span>
      <span class="brand__full">Coherent Lattice of<br>Adaptive Reasoning Method</span>
    </div>
    <div class="contact">
      <p class="contact__name">John Smith</p>
      <p class="contact__title">Managing Director</p>
      <p class="contact__address">1234, Address Goes Here<br>Country Name, 123456</p>
      <ul class="contact__lines">
        <li>
          <svg class="contact__icon" viewBox="0 0 10 10" aria-hidden="true"><path d="M1 3.2C1 2 2.4 1.3 5 1.3S9 2 9 3.2L7.4 4 6.6 3.1H3.4L2.6 4ZM2.5 5 3.6 4h2.8L7.5 5 8 8.7H2Z"/></svg>
          <span>823-456-7890</span>
        </li>
        <li>
          <svg class="contact__icon" viewBox="0 0 10 10" aria-hidden="true"><path d="M1 2.5h8v1L5 6 1 3.5Z M1 4.6 5 7.1 9 4.6V8H1Z"/></svg>
          <span>info@youremail.com</span>
        </li>
      </ul>
    </div>
  </section>

  <section class="card card--back" aria-label="Business card back">
    <h1 class="tagline">
      <span class="tagline__l1">Maximising</span>
      <span class="tagline__l2">Performance</span>
      <span class="tagline__l3">For Highly</span>
      <span class="tagline__l4">Effective</span>
      <span class="tagline__l5">People</span>
    </h1>
    <div class="brand">
      <span class="brand__name">KVOR</span>
      <span class="brand__full">Coherent Lattice of<br>Adaptive Reasoning Method</span>
    </div>
  </section>
</main>
</body>
</html>
```